Health and wellnes company needs business cards

We are a Health and wellness business just relocated to Spain. Here nobody knows our business so we would like to put some of our services on the card. Clean design with logo.

Contact Information for Business Card

Brightmeadow
Paula & Oskar Dunbeck
Calle del Almendro 57
Sanlúcar de Barrameda
Mobile: 0046 731 402687
info@brightmeadow.example

Font styles to use
Serif

Colors
85cae6
85acd3
b768aa

Requirements
Must have
• these Services somewhere on the card
• - Private or group yoga
• - Reconnective healing
• - Kitesurfing lessons
• - Massage
• LOgo somewhere
Nice to have
• Colours that go with the logo please

```html
<!DOCTYPE html>
<html lang="en">
<head>
<meta charset="utf-8">
<title>Brightmeadow business cards</title>
<link rel="stylesheet" href="https://fonts.googleapis.com/css2?family=Marcellus&family=Poppins:wght@300;400&family=Lato:wght@400&display=swap">
<style>
  :root {
    --navy: #183662;
    --teal: #62c3c9;
    --paper: #ffffff;
    --ink-soft: #5c5f66;
    --backdrop: #e9e9eb;
  }
  html, body {
    margin: 0;
    padding: 0;
    width: 1200px;
    height: 862px;
    overflow: hidden;
    background: var(--backdrop);
  }
  .canvas {
    position: relative;
    width: 1200px;
    height: 862px;
  }
  .card {
    position: absolute;
    left: 323px;
    width: 554px;
    height: 317px;
    box-shadow: 0 3px 10px rgba(0,0,0,0.18);
    overflow: hidden;
  }
  .card--front { top: 96px; background: var(--paper); }
  .card--back { top: 449px; background: var(--navy); }

  .accent-bar {
    position: absolute;
    left: 0;
    top: 64px;
    width: 8px;
    height: 54px;
    background: var(--navy);
  }
  .owners {
    position: absolute;
    left: 51px;
    top: 60px;
    margin: 0;
    font-family: "Marcellus", serif;
    font-weight: 400;
    font-size: 21px;
    line-height: 31px;
    color: var(--navy);
    text-transform: uppercase;
    letter-spacing: 0.2px;
  }
  .address {
    position: absolute;
    left: 51px;
    top: 158px;
    margin: 0;
    font-family: "Poppins", sans-serif;
    font-weight: 300;
    font-size: 13.5px;
    line-height: 20px;
    color: var(--ink-soft);
    font-style: normal;
  }
  .contacts {
    position: absolute;
    left: 51px;
    top: 212px;
    margin: 0;
    padding: 0;
    list-style: none;
    font-family: "Poppins", sans-serif;
    font-weight: 300;
    font-size: 13.5px;
    line-height: 20px;
    color: var(--ink-soft);
  }
  .contacts li { display: flex; align-items: center; gap: 7px; }
  .contacts svg { width: 12px; height: 12px; flex: none; }

  .brand {
    position: absolute;
    display: flex;
    flex-direction: column;
    align-items: center;
  }
  .brand__dot {
    width: 92px;
    height: 92px;
    border-radius: 50%;
    border: 5px solid var(--teal);
    box-sizing: border-box;
  }
  .brand__name {
    margin-top: 12px;
    font-family: "Marcellus", serif;
    font-weight: 400;
    font-size: 27px;
    letter-spacing: 0.5px;
    text-transform: uppercase;
    line-height: 1;
  }
  .card--front .brand { left: 262px; top: 100px; width: 258px; }
  .card--front .brand__name { color: var(--navy); }
  .card--back .brand { left: 148px; top: 44px; width: 258px; }
  .card--back .brand__name { color: var(--paper); }

  .services {
    position: absolute;
    left: 0;
    right: 0;
    top: 272px;
    margin: 0;
    text-align: center;
    font-family: "Lato", sans-serif;
    font-size: 12.5px;
    color: var(--paper);
  }
</style>
</head>
<body>
<main class="canvas">
  <section class="card card--front" aria-label="Business card front">
    <div class="accent-bar"></div>
    <h1 class="owners">Paula &amp;<br>Oskar Dunbeck</h1>
    <address class="address">Calle del Almendro 57<br>Sanlúcar de Barrameda</address>
    <ul class="contacts">
      <li>
        <svg viewBox="0 0 12 12" aria-hidden="true"><path d="M2.2 1h2l1 2.6-1.3 1a6.5 6.5 0 0 0 3.5 3.5l1-1.3L11 7.8v2c0 .7-.6 1.2-1.3 1.2A9.5 9.5 0 0 1 1 2.3C1 1.6 1.5 1 2.2 1z" fill="none" stroke="#62c3c9" stroke-width="1.2"/></svg>
        0046 731 402687
      </li>
      <li>
        <svg viewBox="0 0 12 12" aria-hidden="true"><rect x="1" y="2.5" width="10" height="7" fill="none" stroke="#62c3c9" stroke-width="1.1"/><path d="M1 2.8 6 6.6l5-3.8" fill="none" stroke="#62c3c9" stroke-width="1.1"/></svg>
        info@brightmeadow.example
      </li>
    </ul>
    <div class="brand">
      <span class="brand__dot" aria-hidden="true"></span>
      <span class="brand__name">Brightmeadow</span>
    </div>
  </section>

  <section class="card card--back" aria-label="Business card back">
    <div class="brand">
      <span class="brand__dot" aria-hidden="true"></span>
      <span class="brand__name">Brightmeadow</span>
    </div>
    <p class="services">Private or group yoga | Reconnective healing | Kitesurfing lessons | Massage | LOgo somewhere</p>
  </section>
</main>
</body>
</html>
```